Business card design needed

I would like a one sided black business card with the information provided above. Refer to my website www.brightvolleyracquets.com.au for an example of colors I have used for my site, would like to keep this consistent for my business cards also, I will upload my logo below.

I am a new small business that provides tennis customers with racquet re stringing, tennis strings and accessories.

Industry/Entity Type

Small Business

Contact Information for Business Card

Bright Volley Tennis

Owen Whitby
Managing Director

brightvolleyracquets@mailbox.example
www.brightvolleyracquets.com.au
0491 726 305

Racquet Restringing/Tennis Strings/Accessories

Requirements
Must have
• Must have my logo and card must be black

```html
<!DOCTYPE html>
<html lang="en">
<head>
<meta charset="utf-8">
<title>Bright Volley Tennis – Business Card</title>
<link rel="stylesheet" href="https://fonts.googleapis.com/css2?family=Exo+2:wght@400;500;700&display=swap">
<style>
  :root {
    --backdrop: #e8e5e0;
    --card-black: #000000;
    --lime: #b6d333;
    --court-blue: #1f4a8b;
    --white: #ffffff;
    --rule-grey: #8a8a8a;
  }
  * { box-sizing: border-box; margin: 0; padding: 0; }
  html, body {
    width: 1200px;
    height: 475px;
    overflow: hidden;
    background: var(--backdrop);
    font-family: "Exo 2", sans-serif;
  }
  .card {
    position: absolute;
    top: 81px;
    width: 546px;
    height: 313px;
    background: var(--card-black);
    overflow: hidden;
  }
  .card--front { left: 30px; }
  .card--back { left: 602px; }

  .brand {
    position: absolute;
    display: flex;
    align-items: center;
    gap: 12px;
    color: var(--lime);
    font-weight: 700;
    font-size: 31px;
    letter-spacing: 0.5px;
    text-transform: uppercase;
    white-space: nowrap;
    transform: translateX(-50%);
  }
  .brand__dot {
    width: 26px;
    height: 26px;
    border-radius: 50%;
    background: var(--lime);
    flex: none;
  }
  .card--front .brand { left: 282px; top: 78px; }
  .card--back .brand { left: 273px; top: 112px; }

  .holder {
    position: absolute;
    right: 324px;
    top: 192px;
    text-align: right;
    color: var(--lime);
  }
  .holder__name {
    font-size: 18px;
    font-weight: 400;
    letter-spacing: 0.6px;
    text-transform: uppercase;
    line-height: 22px;
  }
  .holder__role {
    font-size: 13.5px;
    line-height: 18px;
  }
  .divider {
    position: absolute;
    left: 257px;
    top: 189px;
    width: 1px;
    height: 74px;
    background: var(--rule-grey);
  }
  .contact {
    position: absolute;
    left: 274px;
    top: 188px;
    list-style: none;
    color: var(--white);
    font-size: 13.5px;
    line-height: 19px;
    letter-spacing: 0.4px;
  }
  .contact__label { display: inline-block; width: 20px; }

  .stripe {
    position: absolute;
    left: 0;
    bottom: 0;
    width: 546px;
    height: 26px;
  }
  .back-url {
    position: absolute;
    left: 0;
    right: 0;
    top: 250px;
    text-align: center;
    color: var(--white);
    font-size: 13.5px;
    letter-spacing: 2.2px;
  }
</style>
</head>
<body>
  <section class="card card--front" aria-label="Business card front">
    <div class="brand"><span class="brand__dot"></span>Bright Volley Tennis</div>
    <div class="holder">
      <p class="holder__name">Owen Whitby</p>
      <p class="holder__role">Managing Director</p>
    </div>
    <div class="divider"></div>
    <ul class="contact">
      <li><span class="contact__label">P</span>: 0491 726 305</li>
      <li><span class="contact__label">E</span>: brightvolleyracquets@mailbox.example</li>
      <li><span class="contact__label">W</span>: www.brightvolleyracquets.com.au</li>
    </ul>
    <svg class="stripe" viewBox="0 0 546 26" preserveAspectRatio="none" aria-hidden="true">
      <polygon points="0,0 243,0 217,26 0,26" fill="var(--court-blue)"/>
      <polygon points="255,0 546,0 546,26 229,26" fill="var(--lime)"/>
    </svg>
  </section>

  <section class="card card--back" aria-label="Business card back">
    <div class="brand"><span class="brand__dot"></span>Bright Volley Tennis</div>
    <p class="back-url">www.brightvolleyracquets.com.au</p>
  </section>
</body>
</html>
```